Design and Renovation Company Luxury Business Card

I want to create a luxury business card for a Design and Renovation Firm . We will use our current logo. The company name is 528BUILDA. We do not want anything standard. We need a very unique concept.
Please see uploaded inspiration. I really like the textured paper option. I would like the card to be thick with debossing, and/or embossing options. The logo has orange in it but I would like to see the card with and without the orange. I think the orange may make the company feel less high-end. The goal is to elevate the logo not match its vibe per se of the logo. We want something very unique, not standard at all!
I would like a space for :
Logo,
Name,
Position,
Email,
Office number,
Website Address,
Business Address,
Thank you!
Have fun!
Target Market(s)
Home owners Age 35 +
Industry/Entity Type
Design and Renovation
Contact Information for Business Card
Logo, Name, Position, Email, Office number, Website Address, Business Address,.
Colors
Designer to choose colors to be used in the design.
Requirements
Must have
- A luxury designer feel. Must be black or dark grey but open to other luxury ideas.
Nice to have
- Gold, silver, black embossing or debossing. Textured paper design.
Should not have
- A cheap look and feel.

```html
<!DOCTYPE html>
<html lang="en">
<head>
<meta charset="utf-8">
<title>528BUILDA Business Card</title>
<link href="https://fonts.googleapis.com/css2?family=Arimo:wght@400;700&display=swap" rel="stylesheet">
<style>
  :root {
    --backdrop: #4b4b4c;
    --card: #262626;
    --tile-dark: #222222;
    --tile-dark-edge: #333333;
    --tile-grey: #555555;
    --orange: #ef8a1c;
    --edge: #d2680f;
    --white: #f2f2f2;
  }
  * { box-sizing: border-box; margin: 0; padding: 0; }
  html, body { width: 1200px; height: 1108px; overflow: hidden; }
  body {
    background: var(--backdrop);
    font-family: "Arimo", Arial, sans-serif;
    color: var(--white);
    position: relative;
  }
  .card {
    position: absolute;
    left: 180px;
    width: 840px;
    height: 480px;
    background: var(--card);
    border-bottom: 4px solid var(--edge);
    overflow: hidden;
  }
  .card--front { top: 44px; }
  .card--back { top: 584px; }

  .company-name {
    font-family: "Arimo", Arial, sans-serif;
    font-weight: 400;
    line-height: 1;
    color: var(--white);
  }

  /* front */
  .card--front .company-name { position: absolute; left: 84px; top: 64px; font-size: 52px; }
  .person { position: absolute; left: 84px; top: 176px; }
  .person__name { font-weight: 700; font-size: 30px; color: var(--orange); }
  .person__role { font-size: 17px; margin-top: 6px; }
  .address { position: absolute; left: 84px; top: 264px; font-size: 19px; line-height: 1.35; font-style: normal; }
  .contacts { position: absolute; left: 84px; top: 346px; list-style: none; font-size: 19px; line-height: 1.5; }
  .contacts li { display: flex; align-items: center; gap: 12px; }
  .contacts svg { width: 16px; height: 16px; flex: none; }

  .tile { position: absolute; }
  .tile--orange { left: 600px; top: 110px; width: 210px; height: 170px; background: var(--orange); }
  .tile--dark {
    left: 378px; top: 296px; width: 206px; height: 164px;
    background: linear-gradient(135deg, var(--tile-dark) 0%, #2c2c2c 100%);
    box-shadow: inset 0 0 0 1px var(--tile-dark-edge);
  }
  .tile--grey { left: 600px; top: 296px; width: 210px; height: 164px; background: var(--tile-grey); }

  /* back */
  .pattern-area {
    position: absolute;
    inset: 0;
    background: linear-gradient(100deg, #101010 0%, #202020 40%, #3a3a3a 75%, #4a4a4a 100%);
  }
  .card--back .company-name { position: absolute; right: 70px; bottom: 92px; font-size: 60px; }
</style>
</head>
<body>
  <section class="card card--front" aria-label="Business card front">
    <div class="company-name">528BUILDA</div>
    <div class="person">
      <div class="person__name">MARCUS ELLERY</div>
      <div class="person__role">President</div>
    </div>
    <address class="address">
      4215 Alder Crest Road<br>Halden, Canada 58210
    </address>
    <ul class="contacts">
      <li>
        <svg viewBox="0 0 16 16" aria-hidden="true"><path d="M4 1 L6.5 4 L5 6 Q6.5 9.5 10 11 L12 9.5 L15 12 L13 15 Q5 14 1 4 Z" fill="var(--orange)"/></svg>
        604-218-7390
      </li>
      <li>
        <svg viewBox="0 0 16 16" aria-hidden="true"><rect x="4" y="1" width="8" height="14" rx="1.5" fill="none" stroke="var(--orange)" stroke-width="1.5"/></svg>
        info@528builda.com
      </li>
      <li>
        <svg viewBox="0 0 16 16" aria-hidden="true"><rect x="1" y="3" width="14" height="10" fill="var(--orange)"/><path d="M1 3 L8 9 L15 3" fill="none" stroke="var(--card)" stroke-width="1.3"/></svg>
        www.528builda.com
      </li>
    </ul>
    <div class="tile tile--orange"></div>
    <div class="tile tile--dark"></div>
    <div class="tile tile--grey"></div>
  </section>

  <section class="card card--back" aria-label="Business card back">
    <div class="pattern-area" role="img" aria-label="Debossed decorative pattern of small squares fading from black to grey"></div>
    <div class="company-name">528BUILDA</div>
  </section>
</body>
</html>
```